Business Card For Halvenmoor Financial Consulting

Hi, I would like a business card designed. Bold, modern.
Please use the same design as the logo. I have also attached the website design to see the overall theme.
Wordmark Font
Color: Hex: #01AEF7

```html
<!DOCTYPE html>
<html lang="en">
<head>
<meta charset="utf-8">
<title>Halvenmoor Financial Consulting – Business Card</title>
<link href="https://fonts.googleapis.com/css2?family=Arimo:ital,wght@0,400;0,700;1,400&display=swap" rel="stylesheet">
<style>
  :root {
    --brand-blue: #01AEF7;
    --brand-blue-deep: #0a8fcf;
    --ink: #0f1d2b;
    --text-grey: #555a60;
    --rule-grey: #6c6c6c;
    --card-white: #f7f7f5;
    --backdrop: #151515;
  }
  * { box-sizing: border-box; margin: 0; padding: 0; }
  html, body {
    width: 1200px; height: 963px; overflow: hidden;
    background: var(--backdrop);
    font-family: "Arimo", Arial, sans-serif;
  }
  .sheet {
    position: relative; width: 1200px; height: 963px;
    display: flex; flex-direction: column; align-items: center;
    justify-content: center; gap: 56px;
  }
  .card {
    position: relative; width: 700px; height: 400px;
    border-radius: 28px; overflow: hidden;
  }
  /* Front */
  .card--front { background: var(--card-white); border-bottom: 5px solid var(--brand-blue); }
  .person { position: absolute; left: 48px; top: 110px; }
  .person__name {
    color: var(--brand-blue); font-weight: 700; font-size: 26px;
    letter-spacing: 0.5px; text-transform: uppercase;
  }
  .person__role { color: var(--text-grey); font-size: 17px; margin-top: 4px; }
  .divider {
    position: absolute; left: 48px; right: 90px; top: 186px;
    height: 1.5px; background: var(--rule-grey);
  }
  .contact { position: absolute; left: 48px; top: 210px; list-style: none; }
  .contact__item {
    display: flex; align-items: center; gap: 12px;
    color: var(--text-grey); font-size: 18px; line-height: 32px;
  }
  .contact__icon { width: 16px; height: 16px; flex: none; }
  .address {
    position: absolute; right: 90px; bottom: 50px; text-align: right;
    color: var(--text-grey); font-size: 19px; line-height: 28px;
  }
  .brand {
    position: absolute; right: 48px; top: 100px;
    display: flex; align-items: center; gap: 12px;
  }
  .brand__mark { width: 26px; height: 26px; background: var(--brand-blue); flex: none; }
  .brand__name {
    color: var(--ink); font-weight: 700; font-size: 20px;
    letter-spacing: 1px; text-transform: uppercase; line-height: 1.2;
  }
  /* Back */
  .card--back {
    background: linear-gradient(135deg, #0bb3f8, #0096ec);
    display: flex; align-items: center; justify-content: center; gap: 16px;
  }
  .card--back .brand__mark { width: 36px; height: 36px; background: var(--brand-blue-deep); }
  .card--back .brand__name { color: var(--brand-blue-deep); font-size: 28px; }
</style>
</head>
<body>
<main class="sheet">
  <section class="card card--front" aria-label="Card front">
    <div class="person">
      <p class="person__name">Marcus Ellery</p>
      <p class="person__role">Manager</p>
    </div>
    <div class="brand">
      <span class="brand__mark"></span>
      <p class="brand__name">Halvenmoor<br>Financial Consulting</p>
    </div>
    <div class="divider"></div>
    <ul class="contact">
      <li class="contact__item">
        <svg class="contact__icon" viewBox="0 0 16 16"><path fill="#01AEF7" d="M3 1l3 3-1.6 1.8c.8 2 2.4 3.6 4.8 4.8L11 9l3 3-2 2.5C6.5 14 2 9.5 1 3z"/></svg>
        555-018-2742
      </li>
      <li class="contact__item">
        <svg class="contact__icon" viewBox="0 0 16 16"><rect x="1" y="3" width="14" height="10" fill="#01AEF7"/><path d="M1 3l7 6 7-6" fill="none" stroke="#fff" stroke-width="1.3"/></svg>
        mail@halvenmoorfc.com
      </li>
      <li class="contact__item">
        <svg class="contact__icon" viewBox="0 0 16 16"><circle cx="8" cy="8" r="7" fill="#01AEF7"/><path d="M1 8h14M8 1c-3 3-3 11 0 14M8 1c3 3 3 11 0 14" fill="none" stroke="#fff" stroke-width="1"/></svg>
        www.halvenmoorfc.com
      </li>
    </ul>
    <p class="address">Your Address<br>City, State, Zip 0000</p>
  </section>

  <section class="card card--back" aria-label="Card back">
    <span class="brand__mark"></span>
    <p class="brand__name">Halvenmoor<br>Financial Consulting</p>
  </section>
</main>
</body>
</html>
```